Create modern and sleek business card for luxury real estate company

We're a "boutique" real estate office looking for a design that gets across a highly modern luxury brand. Blacks and whites are probably the best colors unless we try a silver foil for the logo. I've attached a version of our current logo here. I'd like to swap out the current font on there with Gotham Light Regular.

I'm looking to have one side of the card have the logo with the space for our agents info on the other side.

Target Market(s)

Young professionals in a "luxury" headspace

Industry/Entity Type

Real estate

Contact Information for Business Card

A place for agent name, cell number, website. The slogan "Simply Rethinking Real Estate".

Font styles to use
Other font styles liked:
• Gotham Regular

Colors

Designer to choose only greyscale colors for use in the design.

Requirements
Must have
• Matte black as the background color. Clean lines and use of contrast. A specific design aspect that will use silver foil.
Nice to have
• Up in the air on integrating a QR code
Should not have
• Any houses or other real estate related design (ex: a clip art house)

```html
<!DOCTYPE html>
<html lang="en">
<head>
<meta charset="utf-8">
<title>Halden Realty — Business Card</title>
<link rel="stylesheet" href="https://fonts.googleapis.com/css2?family=Montserrat:wght@300;400;500;600&display=swap">
<style>
  :root {
    --page-bg: #141414;
    --card-bg: #1e1e1e;
    --card-edge: #2a2a2a;
    --foil: #f2f2f2;
    --foil-soft: #cfcfcf;
  }
  * { box-sizing: border-box; margin: 0; padding: 0; }
  html, body {
    width: 1200px; height: 900px; overflow: hidden;
    background: var(--page-bg);
    font-family: "Montserrat", sans-serif;
    color: var(--foil);
  }
  .sheet {
    position: relative; width: 1200px; height: 900px;
    display: flex; flex-direction: column; align-items: center; justify-content: center; gap: 40px;
  }
  .card {
    position: relative; width: 680px; height: 388px;
    background: var(--card-bg);
    border: 1px solid var(--card-edge);
    border-radius: 22px;
  }
  .card--front { display: flex; align-items: center; justify-content: center; }
  .brand { display: flex; align-items: center; gap: 18px; }
  .brand__circle {
    width: 64px; height: 64px; border-radius: 50%;
    border: 2px solid var(--foil);
  }
  .brand__name {
    font-weight: 400; font-size: 40px; letter-spacing: 4px; line-height: 1.05;
    text-transform: uppercase; color: var(--foil);
  }
  .card--back .brand { position: absolute; left: 40px; top: 40px; gap: 12px; }
  .card--back .brand__circle { width: 40px; height: 40px; border-width: 1.5px; }
  .card--back .brand__name { font-size: 20px; letter-spacing: 2px; }
  .agent { position: absolute; left: 40px; top: 150px; }
  .agent__name { font-weight: 600; font-size: 22px; letter-spacing: 1.5px; text-transform: uppercase; }
  .agent__role { font-weight: 300; font-size: 15px; color: var(--foil-soft); margin-top: 2px; }
  .contact { position: absolute; left: 40px; bottom: 40px; list-style: none; }
  .contact__item {
    display: flex; align-items: center; gap: 10px;
    font-weight: 300; font-size: 17px; letter-spacing: 0.5px; line-height: 30px;
  }
  .contact__item svg { width: 14px; height: 14px; flex: none; }
  .seal {
    position: absolute; right: 52px; top: 50%; transform: translateY(-50%);
    width: 270px; height: 270px; border-radius: 50%;
    border: 6px solid var(--foil);
  }
</style>
</head>
<body>
<main class="sheet">
  <section class="card card--front" aria-label="Card front">
    <div class="brand">
      <span class="brand__circle" aria-hidden="true"></span>
      <span class="brand__name">Halden<br>Realty</span>
    </div>
  </section>

  <section class="card card--back" aria-label="Card back">
    <div class="brand">
      <span class="brand__circle" aria-hidden="true"></span>
      <span class="brand__name">Halden<br>Realty</span>
    </div>
    <div class="agent">
      <p class="agent__name">Daniel Brooks</p>
      <p class="agent__role">Director</p>
    </div>
    <ul class="contact">
      <li class="contact__item">
        <svg viewBox="0 0 24 24" fill="none" stroke="currentColor" stroke-width="2"><path d="M5 3h4l2 5-3 2a12 12 0 0 0 6 6l2-3 5 2v4a2 2 0 0 1-2 2A18 18 0 0 1 3 5a2 2 0 0 1 2-2z"/></svg>
        555.014.2290
      </li>
      <li class="contact__item">
        <svg viewBox="0 0 24 24" fill="none" stroke="currentColor" stroke-width="2"><rect x="3" y="5" width="18" height="14" rx="1"/><path d="M3 6l9 7 9-7"/></svg>
        hello@haldenrealty.com
      </li>
      <li class="contact__item">
        <svg viewBox="0 0 24 24" fill="none" stroke="currentColor" stroke-width="2"><circle cx="12" cy="12" r="9"/><path d="M3 12h18M12 3c3 3 3 15 0 18M12 3c-3 3-3 15 0 18"/></svg>
        www.haldenrealty.com
      </li>
    </ul>
    <span class="seal" aria-hidden="true"></span>
  </section>
</main>
</body>
</html>
```